Silver Meadow LLC business card

I help with the Marketing and Sales of various Natural, Organic, Eco Friendly and Healthy Main Stream products to Retail Corporate accounts as well as Independents and Distributors.I also highlight Private label items to these same Retail Corporate accounts.Cherish the Moments, Enjoy Life!

Speciality & Health Sales and Marketing

Target Market(s)

Men and Women

Industry/Entity Type

Business

Contact Information for Business Card

Silver Meadow, LLC
Janet Louise Verhagen
438 West Finch Lane
Ste 4-237
Phoenix, AZ 85047
602-555-0147
jverhagen@plumvale.net

Requirements
Must have
• Nice, femine font
Something in the background or on a side with a softness
Nice to have
• Cherish the Moments, Enjoy Life
Should not have
• Hardness

```html
<!DOCTYPE html>
<html lang="en">
<head>
<meta charset="utf-8">
<title>Silver Meadow LLC business card</title>
<link rel="stylesheet" href="https://fonts.googleapis.com/css2?family=Alegreya:wght@400&display=swap">
<style>
  :root {
    --page: #e9e6e2;
    --card: #161616;
    --card-glow: #2c2b2b;
    --ink: #f4f2f0;
    --accent: #e8702f;
    --muted: #dcd9d6;
  }
  * { box-sizing: border-box; margin: 0; padding: 0; }
  html, body { width: 1200px; height: 900px; overflow: hidden; }
  body {
    background: var(--page);
    font-family: "Alegreya", Georgia, serif;
    position: relative;
  }
  .card {
    position: absolute;
    width: 560px;
    height: 320px;
    border-radius: 10px;
    background: radial-gradient(ellipse 80% 90% at 55% 35%, var(--card-glow) 0%, var(--card) 75%);
    box-shadow: 0 12px 30px rgba(0,0,0,0.18);
  }
  .card-front { left: 40px; top: 110px; }
  .card-back { left: 600px; top: 470px; }

  .front-brand {
    position: absolute;
    left: 0; right: 0; top: 78px;
    display: flex; flex-direction: column; align-items: center; gap: 22px;
  }
  .brand-dot {
    width: 96px; height: 80px;
    border-radius: 50%;
    background: var(--ink);
  }
  .front-brand .brand-name {
    color: var(--ink);
    font-size: 36px;
    letter-spacing: 1px;
    text-transform: uppercase;
  }

  .back-brand {
    position: absolute;
    right: 30px; top: 30px;
    display: flex; flex-direction: column; align-items: flex-end; gap: 8px;
  }
  .back-brand .brand-dot {
    width: 56px; height: 46px;
    background: var(--accent);
    margin-right: 50px;
  }
  .back-brand .brand-name {
    color: var(--accent);
    font-size: 21px;
    text-transform: uppercase;
    letter-spacing: 0.5px;
  }

  .person {
    position: absolute;
    left: 40px; top: 146px;
  }
  .person-name { color: var(--ink); font-size: 27px; line-height: 1.1; }
  .person-title { color: var(--accent); font-size: 16px; margin-top: 3px; }

  .contact {
    position: absolute;
    left: 40px; top: 222px;
    color: var(--muted);
    font-size: 15px;
    line-height: 1.6;
  }
  .contact .label { color: var(--accent); }
</style>
</head>
<body>
  <section class="card card-front">
    <div class="front-brand">
      <div class="brand-dot"></div>
      <div class="brand-name">Silver Meadow, LLC</div>
    </div>
  </section>

  <section class="card card-back">
    <div class="back-brand">
      <div class="brand-dot"></div>
      <div class="brand-name">Silver Meadow, LLC</div>
    </div>

    <div class="person">
      <div class="person-name">Janet Louise Verhagen</div>
      <div class="person-title">Specialty &amp; Health Sales</div>
    </div>

    <div class="contact">
      <p>438 West Finch Lane, Ste 4-237, Phoenix, AZ 85047</p>
      <p><span class="label">T:</span> 602-555-0147</p>
      <p><span class="label">E:</span> jverhagen@plumvale.net</p>
    </div>
  </section>
</body>
</html>
```